high end kitchens , needing new logo and business card design .

im looking a very simple looking design but classy that will stand out , i would like the design to be in the colours black , silver , gold and grey , although all colours dont need to be used in design , back of card to have name on it derek fawcett , address and phone number and website address , maybe fb logo . adrress is 42 mill row , larkmoor , bt19 4qa , 07912488265 , front of the card im open to design , back of card very simple i will want it matt black with silver writing , writing doesnt need to be that big

Target Market(s)

people with kitchen projects .

Industry/Entity Type

Interior Design

Contact Information for Business Card

front of business card th on it with maybe tallow hearths under it wrote smaller , maybe the card to be mate black with the writing in a gloss black or silver

Logo Text

th . tallow hearths

Font styles to use
Sans Serif
Script

Colors
1b1b1b
919191
f6f6f6
848484
ffc214
ec1f27

Requirements
Must have
• clean and simple , not too fussy ,
Nice to have
• n/a
Should not have
• n/a

```html
<!DOCTYPE html>
<html lang="en">
<head>
<meta charset="utf-8">
<title>Tallow Hearths – Business Cards</title>
<link rel="stylesheet" href="https://fonts.googleapis.com/css2?family=Questrial&display=swap">
<style>
  :root {
    --stage: #1b1b1b;
    --card: #141414;
    --card-edge: #262626;
    --gloss-black: #0a0a0a;
    --silver: #f6f6f6;
    --silver-soft: #d9d9d9;
    --grey: #848484;
  }
  * { margin: 0; padding: 0; box-sizing: border-box; }
  html, body {
    width: 1200px;
    height: 738px;
    overflow: hidden;
    background: var(--stage);
  }
  .stage {
    position: relative;
    width: 1200px;
    height: 738px;
    font-family: "Questrial", "Century Gothic", sans-serif;
  }
  .card {
    position: absolute;
    width: 520px;
    height: 297px;
    background: linear-gradient(160deg, #1d1d1d 0%, var(--card) 55%, #0f0f0f 100%);
    border: 1px solid var(--card-edge);
    border-radius: 2px;
  }
  .card--front { left: 150px; top: 90px; }
  .card--back  { left: 530px; top: 350px; }

  .front-mark {
    position: absolute;
    inset: 0;
    display: flex;
    flex-direction: column;
    align-items: center;
    justify-content: center;
    gap: 16px;
  }
  .front-mark .mark-dot {
    width: 40px;
    height: 40px;
    border-radius: 50%;
    background: var(--gloss-black);
  }
  .front-mark .brand-name {
    font-size: 30px;
    letter-spacing: 2px;
    text-transform: uppercase;
    color: var(--gloss-black);
  }

  .back-brand {
    position: absolute;
    left: 44px;
    top: 50px;
    display: flex;
    flex-direction: column;
    align-items: center;
    gap: 10px;
  }
  .back-brand .mark-dot {
    width: 30px;
    height: 30px;
    border-radius: 50%;
    background: var(--silver);
  }
  .back-brand .brand-name {
    font-size: 22px;
    letter-spacing: 1.5px;
    text-transform: uppercase;
    color: var(--silver);
  }

  .contact {
    position: absolute;
    left: 300px;
    top: 92px;
    color: var(--silver-soft);
    font-size: 13px;
    line-height: 1.45;
  }
  .contact .person {
    font-size: 16px;
    letter-spacing: 1px;
    text-transform: uppercase;
    color: var(--silver);
    margin-bottom: 14px;
  }
  .contact .address { margin-top: 12px; }

  .social-square {
    position: absolute;
    left: 62px;
    top: 230px;
    width: 30px;
    height: 30px;
    background: var(--grey);
  }
</style>
</head>
<body>
  <main class="stage">
    <section class="card card--front" aria-label="Card front">
      <div class="front-mark">
        <span class="mark-dot"></span>
        <span class="brand-name">Tallow Hearths</span>
      </div>
    </section>

    <section class="card card--back" aria-label="Card back">
      <div class="back-brand">
        <span class="mark-dot"></span>
        <span class="brand-name">Tallow Hearths</span>
      </div>

      <div class="contact">
        <p class="person">Derek Fawcett</p>
        <p class="phone">07912488265</p>
        <p class="email">info@tallowhearths.com</p>
        <p class="web">www.tallowhearths.com</p>
        <p class="address">42 mill row ,<br>larkmoor , bt19 4qa</p>
      </div>

      <span class="social-square" role="img" aria-label="Social media link"></span>
    </section>
  </main>
</body>
</html>
```